Satchel & Sundial needs new business card design

I need a new business card design. I'm looking for out-of-the-box design which represents the freedom of being a location independent entrepreneur.
I offer coaching, retreats and trips.
I would like to see designs with and without the photo.
Colors I use are black (#000000), green (#25A796) and brown (#D7C38C)
Website satchelandsundial.example

Target Market(s)

location independent entrepreneurs, digital nomads, people looking to swap the 9 to 5 for a lifestyle business

Industry/Entity Type

Business

Contact Information for Business Card

Dorota Falkner
Your Lifestyle Business Coach, Retreat & Trip Leader
http://satchelandsundial.example
hello@satchelandsundial.example
Live a life you don't need a holiday from

Font styles to use
Serif
Sans Serif

Requirements
Must have
• One side should contain only the logo. I would also consider having the "Live a life you don't need a holiday from" on that side too (depending on how it looks)
• Please show both sides on the designs.

```html
<!DOCTYPE html>
<html lang="en">
<head>
<meta charset="utf-8">
<title>Satchel &amp; Sundial – Business Card</title>
<link rel="stylesheet" href="https://fonts.googleapis.com/css2?family=Quicksand:wght@500;700&family=Staatliches&display=swap">
<style>
  :root {
    --backdrop: #2a2a2a;
    --card-gold: #d9c68e;
    --card-gold-light: #e6d7a8;
    --card-gold-dark: #cbb57a;
    --ink: #1c1c1c;
    --teal: #25a796;
    --band-text-gold: #d7c38c;
    --photo-green: #7d8f5a;
    --photo-leaf: #a3ad76;
    --photo-shade: #4f5c3a;
  }
  * { box-sizing: border-box; margin: 0; padding: 0; }
  html, body {
    width: 1200px; height: 900px; overflow: hidden;
    background: var(--backdrop);
  }
  .canvas { position: relative; width: 1200px; height: 900px; }

  .card {
    position: absolute;
    width: 640px; height: 366px;
    border-radius: 22px;
    overflow: hidden;
    background: linear-gradient(135deg, var(--card-gold-light) 0%, var(--card-gold) 45%, var(--card-gold-dark) 100%);
    box-shadow: 0 14px 30px rgba(0,0,0,.45);
  }

  /* Front: logo side */
  .card--front { left: 140px; top: 50px; }
  .brand-name {
    position: absolute; left: 0; right: 0; top: 118px;
    text-align: center;
    font-family: "Quicksand", sans-serif; font-weight: 700;
    font-size: 52px; letter-spacing: 1px;
    color: var(--ink);
  }
  .tagline {
    position: absolute; left: 0; right: 0; bottom: 62px;
    text-align: center;
    font-family: "Quicksand", sans-serif; font-weight: 700;
    font-size: 19px; color: var(--ink);
  }

  /* Back: contact side */
  .card--back { left: 420px; top: 484px; }
  .portrait-area {
    position: absolute; left: 0; top: 90px; width: 360px; height: 276px;
    background:
      radial-gradient(ellipse at 40% 55%, var(--photo-leaf) 0%, var(--photo-green) 45%, var(--photo-shade) 100%);
    -webkit-mask-image: linear-gradient(100deg, #000 55%, transparent 100%);
            mask-image: linear-gradient(100deg, #000 55%, transparent 100%);
  }
  .name-band {
    position: absolute; right: 0; top: 70px;
    width: 400px; height: 62px;
    background: var(--ink);
    clip-path: polygon(6% 0, 100% 0, 100% 100%, 0 100%);
    padding: 8px 0 0 48px;
  }
  .person-name {
    font-family: "Staatliches", sans-serif;
    font-size: 32px; letter-spacing: 4px; line-height: 1;
    color: var(--teal);
  }
  .person-role {
    font-family: "Staatliches", sans-serif;
    font-size: 12.5px; letter-spacing: .6px;
    color: var(--band-text-gold);
    margin-top: 2px;
  }
  .contact {
    position: absolute; right: 34px; top: 178px;
    text-align: right;
    font-family: "Quicksand", sans-serif; font-weight: 700;
    font-size: 15px; line-height: 1.75;
    color: var(--ink);
  }
  .contact .accent { color: var(--teal); }
</style>
</head>
<body>
<main class="canvas">
  <section class="card card--front" aria-label="Card front">
    <div class="brand-name">Satchel &amp; Sundial</div>
    <p class="tagline">Live a life you don't need a holiday from</p>
  </section>

  <section class="card card--back" aria-label="Card back">
    <div class="portrait-area" role="img" aria-label="Photo of the coach sitting on a wooden fence among trees, holding a small sign"></div>
    <div class="name-band">
      <div class="person-name">Dorota Falkner</div>
      <div class="person-role">Your Lifestyle Business Coach, Retreat &amp; Trip Leader</div>
    </div>
    <div class="contact">
      <div>hello@satchelandsundial.example</div>
      <div>www.<span class="accent">satchelandsundial</span>.example</div>
    </div>
  </section>
</main>
</body>
</html>
```